Etikett für Rotweinflasche
Liebe farbkosmos Atelier, wir werden uns bei der endgültigen Etikettengestaltung (finale Größe + Rückseite) noch an Euch melden. Bitte sendet uns euren Kontakt an helga.brandt@morvelli.wine
Zielgruppe
Morvelli Italia ist ein exklusives Boutique-Weingut in Sizilien, das hochqualitative Spitzenweine in kleinen Mengen mit modernster Technologie und stets nachhaltig erzeugt. Wir hinterfragen sowohl in der Agronomie im Weingarten als auch in der Önologie im Weinkeller alle herrschenden Traditionen und trachten danach, stets das beste Endprodukt zu kreieren. Der vulkanische, kalkreiche Boden Siziliens sowie trockene, sonnenreiche und niederschlagsarme Vegetationsperioden sind unsere optimale Basis.
Zielgruppe: Internationale Genussmenschen jeglichen Alters, die sich bewusst auch höherpreisige Weine (um die €30+) gönnen , vor allem kunstaffine young professionals mit Qualitäts-& Nachhaltigkeitsanspruch
Aufgabenstellung
Das Etikett ist für Rotwein-Flaschen (Cabernet Sauvignon / Nero D'Avola / Frappato / Syrah / Cerasuolo / Petit Verdot / sowie einen Bourdeaux-Cuveè aus Cabernet Sauvignon und Petit Verdot) .
Die Flasche ist reinschwarz, sehr hochwertig und schwer.
Flaschenform: Bordeauxflasche siehe technisches Datenblatt
Sleeve über dem Korken: schwarz mit weißer Schrift wie bisher
Zu gestalten ist das Etikett der Vorderseite. Zumindest die jeweilige Rotwein-Sorte ist auch textlich darzustellen (zwecks Scannen mit Trubel-App)
Der Kreativität kann freien Lauf gelassen werden! Unterscheidbarkeit vom Markt ist explizit gewollt.
Unsere aktuellen Etiketten und Markenauftritt siehe: https://morvelli.wine/shop/

```html
<!DOCTYPE html>
<html lang="de">
<head>
<meta charset="UTF-8">
<title>Morvelli Italia – Syrah Etikett</title>
<link rel="stylesheet" href="https://fonts.googleapis.com/css2?family=Cormorant+Garamond:wght@500&display=swap">
<style>
  :root {
    --stage-top: #4a4b50;
    --stage-bottom: #2c2d31;
    --label-light: #d8ecd4;
    --label-lime: #b8d84a;
    --label-green: #3f9a3c;
    --label-deep: #1f5a2e;
    --label-teal: #2f8f86;
    --label-warm: #d9864e;
    --type-dark: #1c2418;
  }
  html, body {
    margin: 0;
    padding: 0;
    width: 1200px;
    height: 900px;
    overflow: hidden;
  }
  body {
    background: radial-gradient(ellipse at 50% 45%, var(--stage-top), var(--stage-bottom) 80%);
    display: flex;
    align-items: center;
    justify-content: center;
  }
  .wine-label {
    position: relative;
    width: 480px;
    height: 580px;
    box-shadow: 0 18px 40px rgba(0, 0, 0, 0.35);
    overflow: hidden;
  }
  .label-artwork {
    position: absolute;
    inset: 0;
    background:
      radial-gradient(circle at 70% 30%, var(--label-warm) 0%, transparent 22%),
      radial-gradient(circle at 60% 45%, var(--label-teal) 0%, transparent 30%),
      radial-gradient(circle at 30% 20%, var(--label-light) 0%, transparent 40%),
      radial-gradient(circle at 20% 75%, var(--label-lime) 0%, transparent 45%),
      linear-gradient(160deg, var(--label-light) 0%, var(--label-lime) 35%, var(--label-green) 65%, var(--label-deep) 100%);
  }
  .varietal-name {
    position: absolute;
    left: 150px;
    bottom: 92px;
    margin: 0;
    font-family: "Cormorant Garamond", serif;
    font-weight: 500;
    font-size: 34px;
    letter-spacing: 0.06em;
    color: var(--type-dark);
  }
</style>
</head>
<body>
  <main class="wine-label">
    <div class="label-artwork" role="img" aria-label="Farbenfrohe Malerei in Grün-, Gelb- und Türkistönen mit fließenden Pinselschwüngen"></div>
    <h1 class="varietal-name">SYRAH</h1>
  </main>
</body>
</html>
```